Kestrelford Therapy and Consulting

Build & publish a WordPress website that advertises and markets my private practice - which is delivering, and consulting in, psychological therapies. I also need to be able to edit content (eg text and images) on the end product thereafter. It should have a call to action on the homepage, links to:
• About me
• For referrers (with link to service fees)
• Contact details – phone#, email address, location, operating hours, and service fees
• Other resources

Target Market(s)

People struggling with mental health, relationships, and/or psychological disorders

Industry/Entity Type

Mental health

Coding

Coded - Design and coding required

Number of Pages Required

4 page

Requirements
Must have
• WordPress
Nice to have
• Please make my logo standout on the home page
Should not have
• No testimonials - they're forbidden for psychologists in Australia

```html
<!DOCTYPE html>
<html lang="en">
<head>
<meta charset="utf-8">
<title>Kestrelford Therapy and Consulting</title>
<link rel="stylesheet" href="https://fonts.googleapis.com/css2?family=Tinos:wght@400;700&family=Roboto:wght@400;500;700&display=swap">
<style>
:root{
  --cyan:#33c3d8;
  --pink:#dc9ede;
  --pink-icon:#d889dc;
  --ink:#1c1c1c;
  --body:#4a4a4a;
  --black:#050505;
  --white:#ffffff;
}
*{box-sizing:border-box;margin:0;padding:0}
html,body{width:1200px;height:5119px;overflow:hidden;background:var(--white)}
body{position:relative;font-family:"Roboto",sans-serif;color:var(--body)}
h1,h2,h3,h4{font-family:"Tinos",serif;color:var(--ink);font-weight:700}

/* header */
.topbar{position:absolute;left:338px;top:0;width:862px;height:74px;background:var(--cyan);border-bottom-left-radius:44px;color:var(--white);font-size:12px}
.topbar .item{position:absolute;top:16px;display:flex;gap:10px}
.topbar .label{font-family:"Tinos",serif;font-weight:700;font-size:15px;line-height:18px}
.topbar .val{line-height:18px}
.logo{position:absolute;left:111px;top:52px;display:flex;align-items:center;gap:10px}
.logo .dot{width:38px;height:38px;border-radius:50%;background:var(--cyan)}
.logo .name{font-family:"Tinos",serif;font-size:25px;color:#333}
.nav{position:absolute;left:387px;top:103px;display:flex;gap:42px;font-family:"Tinos",serif;font-size:15px;color:var(--ink)}
.btn{display:inline-flex;align-items:center;justify-content:center;background:var(--pink);color:var(--white);font-size:14px;font-weight:500}
.get-started{position:absolute;left:966px;top:93px;width:121px;height:38px}

/* hero */
.hero{position:absolute;left:0;top:149px;width:1200px;height:600px;border-radius:0 0 50% 50%/0 0 70px 70px;overflow:hidden;
  background:
    radial-gradient(ellipse 260px 180px at 600px 470px,#e2b9a2 0%,rgba(214,160,134,.75) 45%,rgba(0,0,0,0) 100%),
    radial-gradient(ellipse 300px 220px at 380px 520px,#b77c64 0%,rgba(150,95,75,.6) 50%,rgba(0,0,0,0) 100%),
    radial-gradient(ellipse 320px 260px at 880px 520px,#a9735e 0%,rgba(120,80,66,.6) 50%,rgba(0,0,0,0) 100%),
    radial-gradient(ellipse 380px 260px at 900px 120px,#6a4a48 0%,rgba(60,40,40,0) 100%),
    radial-gradient(ellipse 420px 300px at 200px 200px,#4a3634 0%,rgba(40,30,30,0) 100%),
    linear-gradient(180deg,#2a1f20 0%,#3d2b2a 50%,#5a3e36 100%)}
.hero .shade{position:absolute;inset:0;background:rgba(20,12,14,.28)}
.hero h1{position:absolute;left:0;width:1200px;top:170px;text-align:center;color:var(--white);font-size:76px;line-height:86px}
.hero .cta{position:absolute;left:540px;top:371px;width:120px;height:38px;background:var(--white);color:var(--pink);font-size:14px;border-radius:2px}

/* about */
.photo{position:absolute}
.about-photo{left:111px;top:835px;width:429px;height:445px;
  background:
    radial-gradient(ellipse 130px 160px at 215px 210px,#c9a08a 0%,#b08572 45%,rgba(150,110,95,0) 100%),
    radial-gradient(ellipse 260px 130px at 215px 445px,#355489 0%,#2b4676 60%,rgba(40,70,120,0) 100%),
    radial-gradient(ellipse 140px 160px at 60px 120px,#6d8a4a 0%,rgba(60,80,40,0) 100%),
    radial-gradient(ellipse 140px 160px at 380px 140px,#4f6c3b 0%,rgba(50,70,40,0) 100%),
    linear-gradient(180deg,#2c3d24 0%,#3f5530 45%,#314a6e 100%)}
.tag-box{position:absolute;width:314px;color:var(--white);padding:28px 40px}
.tag-box h3{color:var(--white);font-size:38px;line-height:42px}
.tag-box p{font-size:16px;margin-top:10px}
.qual{left:439px;top:1145px;height:135px;background:var(--pink)}
.text-col{position:absolute;left:612px;width:468px}
.text-col h2{font-size:40px;line-height:44px}
.subtitle{color:var(--cyan);font-weight:500;font-size:19px;margin-top:10px}
.text-col p{font-size:14px;line-height:25.6px;margin-top:10px}

/* services */
.services{position:absolute;left:0;top:1367px;width:1200px;height:946px;
  background:
    radial-gradient(ellipse 500px 400px at 1000px 150px,rgba(232,210,200,.7) 0%,rgba(230,220,215,0) 100%),
    radial-gradient(ellipse 500px 400px at 150px 500px,rgba(214,205,200,.6) 0%,rgba(230,220,215,0) 100%),
    linear-gradient(135deg,#f7f3f2 0%,#ebe8e6 50%,#e6e4e3 100%)}
.section-title{position:absolute;left:0;width:1200px;text-align:center;font-size:40px;line-height:44px}
.lead{position:absolute;left:200px;width:800px;text-align:center;color:var(--cyan);font-size:19px;line-height:28px;font-weight:500}
.card{position:absolute;top:227px;width:303px}
.card .pic{height:240px}
.card h4{text-align:center;font-size:24px;margin-top:22px}
.pic-group{background:
  radial-gradient(ellipse 70px 60px at 150px 140px,#b98a72 0%,rgba(180,130,110,0) 100%),
  radial-gradient(ellipse 90px 120px at 60px 110px,#3e3a3a 0%,rgba(60,55,55,0) 100%),
  radial-gradient(ellipse 90px 120px at 250px 110px,#5a5350 0%,rgba(80,75,70,0) 100%),
  radial-gradient(ellipse 120px 60px at 150px 220px,#8d8e93 0%,rgba(140,140,145,0) 100%),
  linear-gradient(180deg,#d8d4d0 0%,#a7a29e 60%,#6e6a68 100%)}
.pic-assess{background:
  radial-gradient(ellipse 40px 40px at 150px 90px,#bfe6ff 0%,#4aa3e8 50%,rgba(30,100,180,0) 100%),
  radial-gradient(ellipse 140px 30px at 150px 190px,#dfe6ee 0%,rgba(200,210,220,0) 100%),
  radial-gradient(ellipse 180px 140px at 150px 120px,#1d6fc2 0%,rgba(15,60,120,0) 100%),
  linear-gradient(180deg,#0a1c3a 0%,#0f3b73 55%,#06142a 100%)}
.pic-train{background:
  radial-gradient(ellipse 22px 60px at 225px 95px,#6fb8d2 0%,rgba(90,160,190,0) 100%),
  radial-gradient(ellipse 60px 50px at 255px 60px,#f4f1ea 0%,rgba(240,235,225,0) 100%),
  radial-gradient(ellipse 180px 70px at 140px 210px,#3b2a22 0%,rgba(50,35,28,0) 100%),
  radial-gradient(ellipse 90px 140px at 30px 90px,#a0553c 0%,rgba(150,80,60,0) 100%),
  linear-gradient(180deg,#c9b49c 0%,#a78a72 50%,#4a362c 100%)}
.arrow{position:absolute;top:327px;width:38px;height:38px;border-radius:50%;background:var(--cyan)}
.interest{position:absolute;top:670px;width:200px;text-align:center}
.interest svg{display:block;margin:0 auto}
.interest h4{font-size:24px;line-height:34px;margin-top:18px}
.dots{position:absolute;top:856px;left:572px;display:flex;gap:6px;align-items:center}
.dots span{width:6px;height:6px;border-radius:50%;background:#bbb}
.dots .on{width:28px;height:4px;border-radius:2px;background:var(--cyan)}

/* quality band */
.quality{position:absolute;left:0;top:2313px;width:1200px;height:300px;background:var(--cyan);color:var(--white);text-align:center}
.quality h2{color:var(--white);font-size:38px;padding-top:78px}
.quality p{width:900px;margin:20px auto 0;font-size:14px;line-height:26px}

/* approach */
.approach{position:absolute;left:111px;top:2694px;width:475px}
.approach h2{font-size:40px}
.approach p{font-size:14px;line-height:25.4px;margin-top:10px}
.chips{display:flex;flex-wrap:wrap;gap:6px 14px;margin-top:10px;padding-left:18px;font-size:14px;font-weight:500;color:var(--ink)}
.chips span{display:flex;align-items:center;gap:6px}
.chips span::before{content:"";width:6px;height:6px;border-radius:50%;background:var(--cyan)}
.approach-photo{left:658px;top:2700px;width:429px;height:390px;
  background:
    radial-gradient(ellipse 60px 70px at 355px 150px,#d9b3a0 0%,rgba(210,170,150,0) 100%),
    radial-gradient(ellipse 90px 80px at 350px 160px,#3c3e44 0%,#2a2c30 60%,rgba(40,40,45,0) 100%),
    radial-gradient(ellipse 90px 140px at 70px 200px,#7b7c80 0%,rgba(110,110,115,0) 100%),
    radial-gradient(ellipse 70px 80px at 250px 120px,#5d8a45 0%,rgba(80,120,60,0) 100%),
    radial-gradient(ellipse 220px 60px at 215px 330px,#f6f6f6 0%,rgba(240,240,240,0) 100%),
    linear-gradient(180deg,#eef0ee 0%,#dcdcd6 50%,#c7c5c0 100%)}

/* tabs */
.tab{position:absolute;top:3177px;width:255px;height:36px;font-family:"Tinos",serif;font-weight:700;font-size:17px;display:flex;align-items:center;justify-content:center;background:var(--pink);color:var(--white)}
.tab.outline{background:var(--white);color:var(--pink);border:3px solid var(--pink)}
.payment-bg{position:absolute;left:0;top:3260px;width:1200px;height:517px;
  background:
    linear-gradient(180deg,#ffffff 0%,rgba(255,255,255,.92) 22%,rgba(255,255,255,0) 55%),
    radial-gradient(ellipse 40px 90px at 575px 290px,#4fa9c8 0%,rgba(70,150,190,0) 100%),
    radial-gradient(ellipse 500px 110px at 600px 480px,#3a2b25 0%,rgba(50,38,32,0) 100%),
    radial-gradient(ellipse 260px 120px at 200px 430px,#6e4f3f 0%,rgba(100,70,55,0) 100%),
    radial-gradient(ellipse 260px 120px at 1000px 430px,#5e4a40 0%,rgba(90,70,60,0) 100%),
    radial-gradient(ellipse 200px 100px at 900px 200px,#d8cbb8 0%,rgba(210,200,185,0) 100%),
    linear-gradient(180deg,#f2f0ee 0%,#c9b8a8 50%,#7a6252 80%,#3c2f2a 100%)}
.payment-text{position:absolute;left:155px;top:3330px;width:890px;text-align:center;font-size:18.5px;line-height:28px;color:#333}

/* background */
.background-text{position:absolute;left:128px;top:3926px;width:944px;text-align:center;font-size:14px;line-height:26px}

/* referrers */
.ref-photo{left:111px;top:4129px;width:429px;height:487px;
  background:
    radial-gradient(ellipse 60px 70px at 330px 110px,#d2a892 0%,rgba(200,160,140,0) 100%),
    radial-gradient(ellipse 90px 90px at 330px 100px,#8c6a4a 0%,rgba(130,100,70,0) 100%),
    radial-gradient(ellipse 80px 60px at 120px 300px,#6c7280 0%,rgba(100,105,115,0) 100%),
    radial-gradient(ellipse 180px 90px at 160px 330px,#c8c0b6 0%,rgba(200,190,180,0) 100%),
    radial-gradient(ellipse 200px 100px at 215px 470px,#6a5c52 0%,rgba(100,85,75,0) 100%),
    linear-gradient(150deg,#4c4540 0%,#857970 40%,#b9afa5 70%,#d8d3cd 100%)}
.appt{left:439px;top:4451px;height:133px;background:var(--cyan);text-align:center;padding:24px 20px}
.appt p{font-size:15px;line-height:22px;margin-top:8px}
.view-fees{position:absolute;left:612px;top:4373px;width:121px;height:36px}

/* footer */
.footer{position:absolute;left:0;top:4701px;width:1200px;height:418px;background:var(--black);color:var(--white)}
.fcol{position:absolute;top:80px;font-size:14px;line-height:30px}
.fcol h4{color:var(--white);font-size:19px;margin-bottom:14px}
.fcol .row{display:flex;gap:16px;align-items:flex-start;margin-bottom:10px;line-height:22px}
.footer .rule{position:absolute;left:0;top:376px;width:1200px;height:1px;background:#333}
.footer .copy{position:absolute;left:0;top:390px;width:1200px;text-align:center;font-size:13px;font-weight:500}
</style>
</head>
<body>

<header>
  <div class="logo"><span class="dot"></span><span class="name">Kestrelford</span></div>
  <div class="topbar">
    <div class="item" style="left:26px">
      <svg width="14" height="18" viewBox="0 0 14 18"><path d="M7 0C3.1 0 0 3.1 0 7c0 5 7 11 7 11s7-6 7-11c0-3.9-3.1-7-7-7zm0 9.5A2.5 2.5 0 1 1 7 4.5a2.5 2.5 0 0 1 0 5z" fill="#fff"/></svg>
      <div><div class="label">Practice Locations</div><div class="val">Suite 4, Harrow House, 18 Marlow Street, Kestrelford, TAS 7000</div></div>
    </div>
    <div class="item" style="left:466px">
      <svg width="16" height="16" viewBox="0 0 24 24"><path d="M6.6 10.8a15.2 15.2 0 0 0 6.6 6.6l2.2-2.2c.3-.3.7-.4 1-.2 1.1.4 2.3.6 3.6.6.6 0 1 .4 1 1V20c0 .6-.4 1-1 1A17 17 0 0 1 3 4c0-.6.4-1 1-1h3.5c.6 0 1 .4 1 1 0 1.3.2 2.5.6 3.6.1.3 0 .7-.2 1z" fill="#fff"/></svg>
      <div><div class="label">Phone</div><div class="val">0491 570 110</div></div>
    </div>
    <div class="item" style="left:606px">
      <svg width="16" height="14" viewBox="0 0 24 20"><path d="M2 2h20v16H2z" fill="#fff"/><path d="M2 2l10 8 10-8" fill="none" stroke="#33c3d8" stroke-width="2"/></svg>
      <div><div class="label">Email</div><div class="val">info@kestrelford.com</div></div>
    </div>
  </div>
  <nav class="nav"><span>Home</span><span>About Me</span><span>Services</span><span>For Referrers</span><span>Contact Us</span></nav>
  <a class="btn get-started">Get Started</a>
</header>

<section class="hero" role="img" aria-label="Photo of two people holding hands in support">
  <div class="shade"></div>
  <h1>Kestrelford<br>Therapy and Consulting</h1>
  <span class="btn cta">Contact Us</span>
</section>

<section class="about">
  <div class="photo about-photo" role="img" aria-label="Portrait of the clinical psychologist"></div>
  <div class="tag-box qual"><h3>Qualifications</h3><p>BAppSc(Hons), MPsych(Clin)</p></div>
  <div class="text-col" style="top:828px">
    <h2>About Me</h2>
    <div class="subtitle">Clinical Psychologist, Clinical Supervisor</div>
    <p>Kestrelford Therapy and Consulting<br>I'm a clinical psychologist, psychotherapist, EMDR Consultant, and Resource Therapy Practitioner and Trainer. My main interest in therapy is helping people overcome the inner obstacles that cause them emotional pain and suffering, and that maintain behavioural patterns that are damaging or self-defeating. I also like to train, coach and mentor other therapists in effective therapies.</p>
  </div>
</section>

<section class="services">
  <h2 class="section-title" style="top:80px">Our Services</h2>
  <p class="lead" style="top:140px">I provide trauma-focused psychotherapy to clients and consult with other mental health clinicians on their practice of psychotherapy.</p>
  <span class="arrow" style="left:53px"><svg width="38" height="38" viewBox="0 0 38 38"><path d="M22 12l-7 7 7 7" fill="none" stroke="#fff" stroke-width="3"/></svg></span>
  <span class="arrow" style="left:1107px"><svg width="38" height="38" viewBox="0 0 38 38"><path d="M16 12l7 7-7 7" fill="none" stroke="#fff" stroke-width="3"/></svg></span>
  <div class="card" style="left:111px"><div class="pic pic-group" role="img" aria-label="Photo of a support group holding hands"></div><h4>Psychotherapy</h4></div>
  <div class="card" style="left:448px"><div class="pic pic-assess" role="img" aria-label="Photo of a hand holding a tablet with assessment icons"></div><h4>Assessment</h4></div>
  <div class="card" style="left:785px"><div class="pic pic-train" role="img" aria-label="Photo of a trainer presenting to a seated group"></div><h4>Professional Training</h4></div>

  <h2 class="section-title" style="top:590px">Areas Of Special Interest</h2>
  <div class="interest" style="left:71px">
    <svg width="80" height="80" viewBox="0 0 80 80" role="img" aria-label="Capsule icon">
      <g fill="var(--pink-icon)"><rect x="12" y="16" width="56" height="22" rx="11" transform="rotate(-18 40 27)"/><rect x="10" y="44" width="58" height="22" rx="11" transform="rotate(-6 39 55)"/></g>
      <path d="M40 18v20M38 46v20" stroke="#fff" stroke-width="2.5"/>
    </svg>
    <h4>Addiction</h4></div>
  <div class="interest" style="left:283px">
    <svg width="80" height="80" viewBox="0 0 80 80" role="img" aria-label="Stress burst icon">
      <g fill="var(--pink-icon)"><path d="M30 4l4 8 4-8M40 4l4 8 4-8M50 4l-4 8" stroke="var(--pink-icon)" stroke-width="2.5" fill="none"/><circle cx="40" cy="36" r="14"/><path d="M14 78c0-16 12-24 26-24s26 8 26 24z"/><rect x="8" y="26" width="10" height="30" rx="5"/><rect x="62" y="26" width="10" height="30" rx="5"/></g>
    </svg>
    <h4>Anger<br>Related Issues</h4></div>
  <div class="interest" style="left:498px">
    <svg width="80" height="80" viewBox="0 0 80 80" role="img" aria-label="Alert icon">
      <g fill="var(--pink-icon)"><circle cx="34" cy="30" r="15"/><path d="M6 78c0-18 12-26 28-26s28 8 28 26z"/><circle cx="62" cy="40" r="12"/></g>
      <path d="M62 33v8M62 45v2" stroke="#fff" stroke-width="3" stroke-linecap="round"/>
    </svg>
    <h4>Panic Attacks</h4></div>
  <div class="interest" style="left:713px">
    <svg width="80" height="80" viewBox="0 0 80 80" role="img" aria-label="Connected nodes icon">
      <circle cx="40" cy="40" r="24" fill="none" stroke="var(--pink-icon)" stroke-width="3"/>
      <g fill="var(--pink-icon)"><circle cx="40" cy="40" r="12"/><circle cx="40" cy="10" r="7"/><circle cx="40" cy="70" r="7"/><circle cx="10" cy="40" r="7"/><circle cx="70" cy="40" r="7"/><circle cx="19" cy="19" r="6"/><circle cx="61" cy="19" r="6"/><circle cx="19" cy="61" r="6"/><circle cx="61" cy="61" r="6"/></g>
    </svg>
    <h4>Assertiveness</h4></div>
  <div class="interest" style="left:925px">
    <svg width="80" height="80" viewBox="0 0 80 80" role="img" aria-label="Rain cloud icon">
      <g fill="var(--pink-icon)"><circle cx="30" cy="34" r="14"/><circle cx="48" cy="28" r="17"/><rect x="16" y="32" width="50" height="16" rx="8"/></g>
      <path d="M26 56l-4 10M40 56l-4 10M54 56l-4 10" stroke="var(--pink-icon)" stroke-width="4" stroke-linecap="round"/>
    </svg>
    <h4>Depression</h4></div>
  <div class="dots"><span class="on"></span><span></span><span></span></div>
</section>

<section class="quality">
  <h2>Quality Provision</h2>
  <p>I generally start sessions checking with how clients are feeling and coping between sessions, ascertaining whether or not the client believes we are "on track" according to what was agreed in the treatment plan we co-created. I endeavour to maximise the benefit we can obtain from the number of sessions available to us.</p>
</section>

<section class="approach">
  <h2>Approach</h2>
  <p>I believe that using Eye Movement Desensitizing and Reprocessing (EMDR) therapy and Resource Therapy (RT) together addresses almost all mental illness that doesn't involve an organic component. EMDR principally addresses disturbing memories from the past that negatively impact a person in the present. RT addresses resource states (also known as states of mind, parts, ego states, and schema modes) that are putting a person 'out of balance', i.e. they are yielding unwanted emotions or unwanted behaviours that are impairing a person's ability to function.</p>
  <div class="chips"><span>EMDR</span><span>Existential</span><span>Integrative</span><span>Mindfulness</span><span>Person Centred</span><span>Psychodynamic</span><span>Schema Therapy</span><span>CBT</span></div>
</section>
<div class="photo approach-photo" role="img" aria-label="Photo of a therapist on a video session at a desk"></div>

<div class="tab" style="left:111px">Professional Associations</div>
<div class="tab" style="left:473px">Transport And Parking</div>
<div class="tab outline" style="left:833px">Payment Options</div>

<section>
  <div class="payment-bg" role="img" aria-label="Photo of an audience at a training seminar"></div>
  <h2 class="section-title" style="top:3256px">Payment Options</h2>
  <p class="payment-text">I currently accept EFT transfers only. I can process Medicare webclaims online on behalf of clients where they are registered with Medicare, i.e. Medicare already have their bank account details on file to be able to deposit the rebate into.</p>
</section>

<section>
  <h2 class="section-title" style="top:3856px">Background</h2>
  <p class="background-text">When I first started to practice, I felt ill-prepared for the vast range of maladies of the human condition, especially as I was immersed in a setting that had so many suffering from the impact of trauma in childhood. Thus, I embarked on decade long learning plan that got me where I am now –equipped with the therapies my practice-based evidence tells me I need, and that satisfies the need for evidence-based practice. I am now substantially trained in EMDR and Resource Therapies, such that I can effectively treat adult survivors of childhood trauma, and supervise or coach others in trauma focused therapies that are effective alone, or in combination.</p>
</section>

<section>
  <div class="photo ref-photo" role="img" aria-label="Photo of a clinician on a laptop call"></div>
  <div class="tag-box appt"><h3>Appointments</h3><p>Currently I am available between 9am to 5pm on Wednesdays only.</p></div>
  <div class="text-col" style="top:4122px">
    <h2>For Referrers</h2>
    <p>Lorem ipsum dolor sit amet, consectetur adipiscing elit, sed do eiusmod tempor incididunt ut labore et dolore magna aliqua. Ut enim ad minim veniam, quis nostrud exercitation ullamco laboris nisi ut aliquip ex ea commodo consequat. Duis aute irure dolor in reprehenderit in voluptate velit esse cillum dolore eu fugiat nulla pariatur.</p>
  </div>
  <a class="btn view-fees">View Fees</a>
</section>

<footer class="footer">
  <div class="fcol" style="left:111px;width:290px">
    <h4>Fees</h4>
    <p style="line-height:25px">My standard fee for a 50 to 60 minute psychological therapy session is $220. For those who are on low or no income my concession fee is $180. Medicare currently rebates 137.05 for a 50+ minute psychological therapy session if a MHCP is in place.</p>
  </div>
  <div class="fcol" style="left:461px">
    <h4>Qulik Links</h4>
    <div>Home</div><div>About Me</div><div>Services</div><div>For Referrers</div><div>Contact Us</div>
  </div>
  <div class="fcol" style="left:661px;width:240px">
    <h4 style="margin-left:30px">Contact Us</h4>
    <div class="row"><svg width="14" height="14" viewBox="0 0 24 24"><path d="M6.6 10.8a15.2 15.2 0 0 0 6.6 6.6l2.2-2.2c.3-.3.7-.4 1-.2 1.1.4 2.3.6 3.6.6.6 0 1 .4 1 1V20c0 .6-.4 1-1 1A17 17 0 0 1 3 4c0-.6.4-1 1-1h3.5c.6 0 1 .4 1 1 0 1.3.2 2.5.6 3.6.1.3 0 .7-.2 1z" fill="#fff"/></svg><span>0491 570 110</span></div>
    <div class="row" style="margin-top:18px"><svg width="14" height="12" viewBox="0 0 24 20"><path d="M2 2h20v16H2z" fill="#fff"/><path d="M2 2l10 8 10-8" fill="none" stroke="#050505" stroke-width="2"/></svg><span>info@kestrelford.com</span></div>
    <div class="row" style="margin-top:18px"><svg width="14" height="18" viewBox="0 0 14 18"><path d="M7 0C3.1 0 0 3.1 0 7c0 5 7 11 7 11s7-6 7-11c0-3.9-3.1-7-7-7zm0 9.5A2.5 2.5 0 1 1 7 4.5a2.5 2.5 0 0 1 0 5z" fill="#fff"/></svg><span>Suite 4, Harrow House, 18<br>Marlow Street, Kestrelford,<br>TAS 7000</span></div>
  </div>
  <div class="fcol" style="left:938px;width:170px">
    <h4>Operating Hours</h4>
    <p style="font-size:13px;line-height:25px">Currently I am available between 9am to 5pm on Wednesdays only.</p>
  </div>
  <div class="rule"></div>
  <div class="copy">© 2024 Kestrelford</div>
</footer>

</body>
</html>
```